lofty birch website

We need a new website for our new business division. We are a sustainable design firm specializing in servicing the needs if architects and developers. We have a staff consisting of architects, engineers, and former contractors and we understand green must make sense.

Bottomline - the only sustainable and lofty birch solutions are those thatbare good for the environment and good for our clients bottom line.

Our company is lofty birch and we will send you a copy of our logo you will see our tagline. Is simple. sustainable. solutions. The play with the periods is that we believe their are simple sustainable solutions and we want to use the words together and possible let each stand alone to accentuate their individual meaning in regards to benefit to our clients.

We want a cool splash page with nich graphics and pictures then later pages to feature projects and design ideas.

Target Market(s)

Our target customers are architects, developers, and contractors who would need assistance with the design process for a VARO project or assisatnce with a building owner who wants to make tehir facilty more environmentally friendly and save energy costs at the same tiem.

Industry/Entity Type

Environment

Requirements
Must have
• Needs a construction look with an environmentally friendly surrounding that is pleasing to look at. Must appeal to the client not only as environmentally friendly but also a wise investment.
Nice to have
• Opportunity for a connection to Social networking including a blog.
Should not have
• A totally environmental building feel at whatever cost. We want to emphasize that it is possible to build environmental friendly and save you money over the life of your building

```html
<!DOCTYPE html>
<html lang="en">
<head>
<meta charset="utf-8">
<title>lofty birch — Projects</title>
<link href="https://fonts.googleapis.com/css2?family=PT+Sans+Narrow:wght@400;700&family=Arimo:wght@400;700&display=swap" rel="stylesheet">
<style>
:root{
  --canvas:#f7f7f7;
  --page:#ffffff;
  --page-edge:#dcdcdc;
  --green:#6cb31a;
  --green-dark:#5a9a12;
  --ink:#3a3a3a;
  --body:#555555;
  --muted:#8a8a8a;
  --rule:#e4e4e4;
  --thumb-frame:#c9c9c9;
  --footer-top:#ececec;
  --footer-bottom:#d6d6d6;
  --footer-head:#dedede;
  --bar-top:#4a4a4a;
  --bar-bottom:#2c2c2c;
  --head-font:"PT Sans Narrow", "Arial Narrow", sans-serif;
  --body-font:"Arimo", Arial, sans-serif;
}
*{box-sizing:border-box;margin:0;padding:0}
html,body{width:900px;height:1200px;overflow:hidden;background:var(--canvas)}
.site{position:absolute;left:197px;top:15px;width:495px;height:1172px;background:var(--page);border:1px solid var(--page-edge);}

/* header */
.contact-tab{position:absolute;left:346px;top:-1px;width:124px;height:18px;border:1px solid var(--page-edge);border-top:none;background:#f6f6f6;font:700 9px var(--head-font);color:var(--green);display:flex;align-items:center;justify-content:space-between;padding:0 10px 0 27px;text-transform:uppercase;white-space:nowrap}
.contact-tab svg{width:9px;height:6px}
.brand{position:absolute;left:16px;top:26px;display:flex;align-items:center;gap:7px}
.brand-dot{width:26px;height:26px;border-radius:50%;background:var(--green)}
.brand-name{font:400 21px/1 var(--head-font);color:var(--ink);white-space:nowrap}
.main-nav{position:absolute;left:259px;top:34px;display:flex;gap:7px;align-items:center}
.main-nav a{font:400 9px var(--head-font);color:#222;text-decoration:none;text-transform:uppercase;padding:2px 3px;white-space:nowrap}
.main-nav a.is-active{background:var(--green);color:#fff}

/* project rows */
.project-group{position:absolute;left:12px;width:483px;height:226px;border-bottom:1px solid var(--rule)}
.project-group h2{position:absolute;left:8px;top:13px;font:400 15px var(--head-font);color:var(--green);text-transform:uppercase;white-space:nowrap}
.cards{position:absolute;left:8px;top:42px;display:flex;gap:17px}
.card{width:100px}
.thumb{width:100px;height:70px;border:1px solid var(--thumb-frame);padding:2px;background:#fff}
.thumb span{display:block;width:100%;height:100%}
.tone-hall{background:linear-gradient(160deg,#cfd8e3,#7d8ea3 55%,#b7a7a9)}
.tone-room{background:linear-gradient(180deg,#f2f2f2,#d8d8d8 60%,#e9e9e9)}
.tone-glass{background:linear-gradient(135deg,#9fb2bf,#4d6473 50%,#c4d0d6)}
.tone-library{background:linear-gradient(180deg,#6a4a2a,#d8a455 55%,#f1d9a8)}
.card h3{margin-top:6px;font:400 11px var(--head-font);color:var(--ink);text-transform:uppercase;padding-left:2px;white-space:nowrap}
.card p{margin-top:3px;width:94px;font:400 6.6px/9px var(--body-font);color:var(--body);padding-left:2px}
.card .more-link{display:block;font:400 6.6px/9px var(--body-font);color:var(--green);padding-left:2px}
.btn{display:flex;align-items:center;justify-content:center;width:50px;height:19px;margin-top:9px;background:var(--green);color:#fff;font:400 8px var(--head-font);text-transform:uppercase;white-space:nowrap}
.pager{position:absolute;right:29px;top:208px;display:flex;gap:3px}
.pager i{width:5px;height:5px;border-radius:50%;background:#c6e3a3}
.pager i:first-child{background:var(--green)}

/* footer */
.site-footer{position:absolute;left:0;top:968px;width:493px;height:153px;background:linear-gradient(180deg,var(--footer-top),var(--footer-bottom));display:flex}
.footer-col{position:relative;border-right:1px solid #c8c8c8}
.footer-col:last-child{border-right:none}
.footer-col h4{height:27px;background:var(--footer-head);font:400 11px/27px var(--head-font);color:#555;text-transform:uppercase;padding-left:10px;border-bottom:1px solid #cfcfcf}
.col-nav h4{padding-left:21px}
.col-nav{width:124px}.col-quote{width:122px}.col-blog{width:122px}.col-address{width:125px}
.col-nav ul{list-style:none;margin:9px 0 0 18px}
.col-nav li{font:400 6.8px/14.7px var(--body-font);color:#555;text-transform:uppercase;display:flex;align-items:center;gap:7px}
.col-nav li::before{content:"";width:5px;height:5px;border-radius:50%;background:var(--green)}
.quote-mark{position:absolute;font:700 26px/1 Georgia,serif;color:#b5b5b5}
.quote-open{left:8px;top:32px}.quote-close{right:10px;top:126px}
.col-quote blockquote{margin:24px 12px 0 15px;font:400 6.6px/9.4px var(--body-font);color:#555}
.col-quote cite{display:block;margin:3px 0 0 15px;font:700 6.6px/9px var(--body-font);color:var(--green);font-style:normal}
.col-quote .role{margin-left:15px;font:400 6.6px var(--body-font);color:#555}
.blog-item{display:flex;gap:8px;margin:10px 0 0 9px;height:24px}
.blog-item + .blog-item{margin-top:10px}
.blog-thumb{width:24px;height:24px;background:#8f8f8f;border:1px solid #fff;flex:none}
.blog-item b{display:block;font:700 6.4px/9px var(--body-font);color:var(--green)}
.blog-item p{width:74px;font:400 6.4px/9px var(--body-font);color:#555}
.col-address address{font-style:normal;margin:10px 0 0 9px;font:400 6.6px/9.7px var(--body-font);color:#555}
.col-address strong{color:var(--green);text-transform:uppercase}
.col-address .gap{display:block;height:9px}
.follow-bar{position:absolute;left:0;top:1121px;width:493px;height:49px;background:linear-gradient(180deg,var(--bar-top),var(--bar-bottom))}
.follow-bar h5{position:absolute;left:17px;top:9px;font:400 12.5px var(--head-font);color:#fff;white-space:nowrap}
.social{position:absolute;left:100px;top:9px;display:flex;gap:4px}
.social span{width:16px;height:16px;background:#9a9a9a;border-radius:2px}
.copyright{position:absolute;left:17px;top:35px;font:400 6px var(--body-font);color:#8a8a8a;white-space:nowrap}
</style>
</head>
<body>
<div class="site">
  <div class="contact-tab">Contact us today!
    <svg viewBox="0 0 9 6"><path d="M1 1l3.5 3.5L8 1" fill="none" stroke="#6cb31a" stroke-width="1.6"/></svg>
  </div>

  <div class="brand"><span class="brand-dot"></span><span class="brand-name">lofty birch</span></div>

  <nav class="main-nav">
    <a>Firm</a><a>Services</a><a class="is-active">Projects</a><a>Your Impact</a><a>Blog</a>
  </nav>

  <section class="project-group" style="top:67px">
    <h2>Commerical Projects</h2>
    <div class="cards">
      <article class="card"><div class="thumb"><span class="tone-hall" role="img" aria-label="Photo of a bright commercial atrium"></span></div><h3>Commerical 1</h3><p>Lorem ipsum dolor sit amet, consectetur adipisicing elit, sed do eiusmod tempo incidid.</p><a class="more-link">Find out more.</a><a class="btn">Read more</a></article>
      <article class="card"><div class="thumb"><span class="tone-room" role="img" aria-label="Photo of a white interior with a screen"></span></div><h3>Commerical 2</h3><p>Lorem ipsum dolor sit amet, consectetur adipisicing elit, sed do eiusmod tempo incidid.</p><a class="more-link">Find out more.</a><a class="btn">Read more</a></article>
      <article class="card"><div class="thumb"><span class="tone-glass" role="img" aria-label="Photo of a glass facade"></span></div><h3>Commerical 3</h3><p>Lorem ipsum dolor sit amet, consectetur adipisicing elit, sed do eiusmod tempo incidid.</p><a class="more-link">Find out more.</a><a class="btn">Read more</a></article>
      <article class="card"><div class="thumb"><span class="tone-library" role="img" aria-label="Photo of a warm-lit library hall"></span></div><h3>Commerical 4</h3><p>Lorem ipsum dolor sit amet, consectetur adipisicing elit, sed do eiusmod tempo incidid.</p><a class="more-link">Find out more.</a><a class="btn">Read more</a></article>
    </div>
    <div class="pager"><i></i><i></i><i></i></div>
  </section>

  <section class="project-group" style="top:293px">
    <h2>Residental Projects</h2>
    <div class="cards">
      <article class="card"><div class="thumb"><span class="tone-hall" role="img" aria-label="Photo of a bright atrium"></span></div><h3>Residental 1</h3><p>Lorem ipsum dolor sit amet, consectetur adipisicing elit, sed do eiusmod tempo incidid.</p><a class="more-link">Find out more.</a><a class="btn">Read more</a></article>
      <article class="card"><div class="thumb"><span class="tone-room" role="img" aria-label="Photo of a white interior with a screen"></span></div><h3>Residental 2</h3><p>Lorem ipsum dolor sit amet, consectetur adipisicing elit, sed do eiusmod tempo incidid.</p><a class="more-link">Find out more.</a><a class="btn">Read more</a></article>
      <article class="card"><div class="thumb"><span class="tone-glass" role="img" aria-label="Photo of a glass facade"></span></div><h3>Residental 3</h3><p>Lorem ipsum dolor sit amet, consectetur adipisicing elit, sed do eiusmod tempo incidid.</p><a class="more-link">Find out more.</a><a class="btn">Read more</a></article>
      <article class="card"><div class="thumb"><span class="tone-library" role="img" aria-label="Photo of a warm-lit library hall"></span></div><h3>Residental 4</h3><p>Lorem ipsum dolor sit amet, consectetur adipisicing elit, sed do eiusmod tempo incidid.</p><a class="more-link">Find out more.</a><a class="btn">Read more</a></article>
    </div>
    <div class="pager"><i></i><i></i><i></i></div>
  </section>

  <section class="project-group" style="top:519px">
    <h2>Industrial Projects</h2>
    <div class="cards">
      <article class="card"><div class="thumb"><span class="tone-hall" role="img" aria-label="Photo of a bright atrium"></span></div><h3>Industrial 1</h3><p>Lorem ipsum dolor sit amet, consectetur adipisicing elit, sed do eiusmod tempo incidid.</p><a class="more-link">Find out more.</a><a class="btn">Read more</a></article>
      <article class="card"><div class="thumb"><span class="tone-room" role="img" aria-label="Photo of a white interior with a screen"></span></div><h3>Industrial 2</h3><p>Lorem ipsum dolor sit amet, consectetur adipisicing elit, sed do eiusmod tempo incidid.</p><a class="more-link">Find out more.</a><a class="btn">Read more</a></article>
      <article class="card"><div class="thumb"><span class="tone-glass" role="img" aria-label="Photo of a glass facade"></span></div><h3>Industrial 3</h3><p>Lorem ipsum dolor sit amet, consectetur adipisicing elit, sed do eiusmod tempo incidid.</p><a class="more-link">Find out more.</a><a class="btn">Read more</a></article>
      <article class="card"><div class="thumb"><span class="tone-library" role="img" aria-label="Photo of a warm-lit library hall"></span></div><h3>Industrial 4</h3><p>Lorem ipsum dolor sit amet, consectetur adipisicing elit, sed do eiusmod tempo incidid.</p><a class="more-link">Find out more.</a><a class="btn">Read more</a></article>
    </div>
    <div class="pager"><i></i><i></i><i></i></div>
  </section>

  <section class="project-group" style="top:746px;border-bottom:none">
    <h2>Institutional Projects</h2>
    <div class="cards">
      <article class="card"><div class="thumb"><span class="tone-hall" role="img" aria-label="Photo of a bright atrium"></span></div><h3>Institutional 1</h3><p>Lorem ipsum dolor sit amet, consectetur adipisicing elit, sed do eiusmod tempo incidid.</p><a class="more-link">Find out more.</a><a class="btn">Read more</a></article>
      <article class="card"><div class="thumb"><span class="tone-room" role="img" aria-label="Photo of a white interior with a screen"></span></div><h3>Institutional 2</h3><p>Lorem ipsum dolor sit amet, consectetur adipisicing elit, sed do eiusmod tempo incidid.</p><a class="more-link">Find out more.</a><a class="btn">Read more</a></article>
      <article class="card"><div class="thumb"><span class="tone-glass" role="img" aria-label="Photo of a glass facade"></span></div><h3>Institutional 3</h3><p>Lorem ipsum dolor sit amet, consectetur adipisicing elit, sed do eiusmod tempo incidid.</p><a class="more-link">Find out more.</a><a class="btn">Read more</a></article>
      <article class="card"><div class="thumb"><span class="tone-library" role="img" aria-label="Photo of a warm-lit library hall"></span></div><h3>Institutional 4</h3><p>Lorem ipsum dolor sit amet, consectetur adipisicing elit, sed do eiusmod tempo incidid.</p><a class="more-link">Find out more.</a><a class="btn">Read more</a></article>
    </div>
    <div class="pager"><i></i><i></i><i></i></div>
  </section>

  <footer class="site-footer">
    <div class="footer-col col-nav">
      <h4>Navigation</h4>
      <ul><li>Home</li><li>Firm</li><li>Services</li><li>Projects</li><li>Your Impact</li><li>Blog</li><li>Contact Us</li></ul>
    </div>
    <div class="footer-col col-quote">
      <h4>Testimonials</h4>
      <span class="quote-mark quote-open">&ldquo;</span>
      <blockquote>Lorem ipsum dolor sit amet, consectetur adipisicing elit, sed do eiusmod tempor incidid ut labore et dolore magna tofik aliqua. Ut enim ad minim heds veniam. Lorem ipsum dolor sit amet, consectetur adipisicing.</blockquote>
      <cite>Dana Reyes</cite>
      <div class="role">Director of XXXX</div>
      <span class="quote-mark quote-close">&rdquo;</span>
    </div>
    <div class="footer-col col-blog">
      <h4>Our Blog</h4>
      <div class="blog-item"><span class="blog-thumb" role="img" aria-label="Blog post image"></span><div><b>Blog post Title 1</b><p>amet, consectetur ing elit, sed do eiusmod.</p></div></div>
      <div class="blog-item"><span class="blog-thumb" role="img" aria-label="Blog post image"></span><div><b>Blog post Title 2</b><p>amet, consectetur ing elit, sed do eiusmod.</p></div></div>
      <div class="blog-item"><span class="blog-thumb" role="img" aria-label="Blog post image"></span><div><b>Blog post Title 1</b><p>amet, consectetur ing elit, sed do eiusmod.</p></div></div>
    </div>
    <div class="footer-col col-address">
      <h4>Address</h4>
      <address><strong>Lofty Birch</strong><br>Number X Street<br>Somewhere City<br>Somewhere County<br>Country<br>Postcode<span class="gap"></span>Phone: (0) 1460 552918<br>Email: info@loftybirch.com</address>
    </div>
  </footer>

  <div class="follow-bar">
    <h5>Follow Us Today!</h5>
    <div class="social"><span aria-label="Social network link"></span><span aria-label="Social network link"></span><span aria-label="Social network link"></span><span aria-label="News feed link"></span></div>
    <div class="copyright">© 2011 Lofty Birch. All rights reserved</div>
  </div>
</div>
</body>
</html>
```